Web Design Velmora Tech

• An Overview of Velmora Tech for reference: We use to be a component manufacturing company. We sold to customers in USA and manage the builds in China using many manufacturing partners. We had a web site that served this market but we have transitioned over the last several years into “A unique design, development and program management company” It is this message we want to put up on the web now. We provide the design support, we help develop and test a new product for our customers and we provide the manufactured produce once we have transitioned it into production.
• The Target Market: Our customers are all high tech. Each product we produce is custom designed and sold only to one a specific customer. We work with a limited number of customer and sell to new customers by word of mouth and referrals. The web site is to provide a back ground check of any new referral so they can see who we are and our basic capabilities. It is not designed to sell customers or to find new customers but provide a background check to new potential customers.
• Pages Required: We estimate 12:
o Home/Title page is page 1 of PDF. It would have buttons to select other pages
o Names of other pages would be (short titles below if on button, if pull down menu the full title of slide)
 USA Facilities
 China Facilities
 Enclosures
 Antennas
 Connectors
 Cables
 EMI Shields
 Overlays
 Process Development
 BrisaLink
 Contact Us (???) >> new page which we are not sure if we should or should not add.
• Design Specifics; attached is our logo, a PDF and PowerPoint slides showing the views we desire. We like these layouts, but perhaps a better one may be suggested for some artistic reason or layout. It should be clean, simple and user intuitive. We like the off white background and use for most of our presentations. One should be able to go from any screen to any other screen. The quote must include both design and implementation onto our web site which is http://velmoratechworks.example/
• Design Process:
We would like to see concepts of the Landing/Homepage, and an internal page initially. Feedback will be provided and you will be asked to continue if your layout is on the correct track.

• Implementation: Desire designer/implimentor to set up on their server. Allow us to test and edit on their site. We will provide password for implementation on our site after final approval.

Target Market(s)

• The Target Market: see above task descripiton

Industry/Entity Type

It Company

Requirements
Must have
• • Pages Required: We estimate 12:
 USA Facilities
 China Facilities
 Enclosures
 Antennas
 Connectors
 Cables
 EMI Shields
 Overlays
 Process Development
 BrisaLink

Must have the implementation phase include in quote. see task description above
Should not have
• Should not be complex or long time loading.
Do not want any twitter or promotional add on functions.

```html
<!DOCTYPE html>
<html lang="en">
<head>
<meta charset="utf-8">
<title>Velmora Tech – China Facilities</title>
<link rel="stylesheet" href="https://fonts.googleapis.com/css2?family=PT+Sans:wght@400;700&display=swap">
<style>
:root{
  --page:#f1f1ef;
  --band:#e3e3e1;
  --ink:#5a5a5a;
  --ink-dark:#3a3a3a;
  --blue:#0f6fb8;
  --nav-top:#5a5a5a;
  --nav-bottom:#383838;
  --nav-text:#f2f2f2;
  --rule:#bdbdbd;
  --frame:#4a4a4a;
}
*{box-sizing:border-box;margin:0;padding:0}
html,body{width:1200px;height:1121px;overflow:hidden}
body{background:var(--page);font-family:"PT Sans",sans-serif;color:var(--ink);position:relative}
.site-address{position:absolute;top:18px;right:89px;display:flex;font-size:14.5px;line-height:23px}
.site-address address{font-style:normal;padding:0 16px}
.site-address .us{text-align:right;border-right:1px solid var(--rule)}
.site-address .cn{padding-right:0}
.brand{position:absolute;left:90px;top:80px;width:208px;height:212px;display:flex;align-items:center;gap:10px}
.brand-mark{width:34px;height:34px;background:var(--blue);flex:none}
.brand-name{color:var(--blue);font-weight:700;font-size:38px;line-height:40px}
.main-nav{position:absolute;left:90px;top:300px;width:208px;height:470px;background:linear-gradient(var(--nav-top),var(--nav-bottom));padding-top:17px}
.main-nav a{display:flex;align-items:center;height:37.6px;color:var(--nav-text);text-decoration:none;font-size:14.6px;padding-left:20px}
.main-nav a svg{margin-right:17px}
.main-nav a.current{font-weight:700}
.contact-box{position:absolute;left:90px;top:779px;width:208px;height:221px;background:linear-gradient(var(--nav-top),var(--nav-bottom));color:#f2f2f2;padding:14px 0 0 16px}
.contact-title{display:flex;align-items:center;gap:8px;margin-left:-6px}
.contact-title h2{font-size:22px;line-height:26px;font-weight:700}
.contact-box dl{margin-top:18px;font-size:16.5px;font-weight:700;color:#e6e6e6}
.contact-box .row{display:flex;height:33px}
.contact-box dt{width:52px}
.contact-box .email{display:block;height:auto;margin-top:2px}
.contact-box .email dd{font-size:13px;margin-top:2px}
.hero{position:absolute;left:314px;top:80px;width:797px;height:452px;border:3px solid var(--frame);overflow:hidden}
.hero-photo{position:absolute;inset:0;background:linear-gradient(170deg,#c9c4ba 0%,#a79c8c 40%,#6e5a44 70%,#3f3226 100%)}
.hero-caption{position:absolute;left:0;right:0;bottom:0;height:94px;background:rgba(25,25,25,.82);color:#fff;font-size:20px;font-weight:700;line-height:29px;padding:21px 0 0 26px}
.hero-next{position:absolute;right:24px;bottom:33px}
.content{position:absolute;left:314px;top:550px;width:797px}
.content h1{color:var(--blue);font-size:23px;font-weight:400;line-height:30px}
.content p{font-size:14.5px;line-height:25px;text-align:justify}
.intro{display:flex;gap:22px;margin-top:7px}
.intro p{width:558px}
.facility-photo{width:218px;height:131px;border:4px solid #fff;box-shadow:0 0 2px rgba(0,0,0,.35);background:linear-gradient(#e6ecef,#b8c4cc 55%,#7d8a95);margin-top:-3px}
.body-para{margin-top:11px}
.service-list{list-style:none;margin-top:19px;display:grid;grid-template-columns:398px 1fr;grid-auto-flow:column;grid-template-rows:repeat(4,35.5px)}
.service-list li{color:var(--blue);font-size:15.6px;font-weight:700;line-height:22px}
.service-list li::before{content:"•";margin-right:8px}
.site-footer{position:absolute;left:0;top:1028px;width:1200px;height:93px;background:var(--band);text-align:center;font-size:13.5px;color:var(--ink-dark)}
.footer-nav{padding-top:22px}
.footer-nav a{color:var(--ink-dark);text-decoration:none}
.footer-nav span{margin:0 8px}
.copyright{margin-top:13px}
</style>
</head>
<body>
<header>
  <div class="site-address">
    <address class="us">48 Orchard Bend, Suite 210<br>Larkfield, CA - 90417</address>
    <address class="cn">Harbor District, Lianshui Road #17<br>Qinghe, China - 200418</address>
  </div>
  <div class="brand"><span class="brand-mark"></span><span class="brand-name">Velmora Tech</span></div>
</header>

<nav class="main-nav">
  <a href="#" class="current"><svg width="7" height="10" viewBox="0 0 7 10"><path d="M1 1l4 4-4 4" fill="none" stroke="#fff" stroke-width="2"/></svg>Home</a>
  <a href="#"><svg width="7" height="10" viewBox="0 0 7 10"><path d="M1 1l4 4-4 4" fill="none" stroke="#fff" stroke-width="2"/></svg>USA Facilities</a>
  <a href="#"><svg width="7" height="10" viewBox="0 0 7 10"><path d="M1 1l4 4-4 4" fill="none" stroke="#fff" stroke-width="2"/></svg>China Facilities</a>
  <a href="#"><svg width="7" height="10" viewBox="0 0 7 10"><path d="M1 1l4 4-4 4" fill="none" stroke="#fff" stroke-width="2"/></svg>Enclosures</a>
  <a href="#"><svg width="7" height="10" viewBox="0 0 7 10"><path d="M1 1l4 4-4 4" fill="none" stroke="#fff" stroke-width="2"/></svg>Antennas</a>
  <a href="#"><svg width="7" height="10" viewBox="0 0 7 10"><path d="M1 1l4 4-4 4" fill="none" stroke="#fff" stroke-width="2"/></svg>Connectors</a>
  <a href="#"><svg width="7" height="10" viewBox="0 0 7 10"><path d="M1 1l4 4-4 4" fill="none" stroke="#fff" stroke-width="2"/></svg>Cables</a>
  <a href="#"><svg width="7" height="10" viewBox="0 0 7 10"><path d="M1 1l4 4-4 4" fill="none" stroke="#fff" stroke-width="2"/></svg>EMI Shields</a>
  <a href="#"><svg width="7" height="10" viewBox="0 0 7 10"><path d="M1 1l4 4-4 4" fill="none" stroke="#fff" stroke-width="2"/></svg>Overlays</a>
  <a href="#"><svg width="7" height="10" viewBox="0 0 7 10"><path d="M1 1l4 4-4 4" fill="none" stroke="#fff" stroke-width="2"/></svg>Process Development</a>
  <a href="#"><svg width="7" height="10" viewBox="0 0 7 10"><path d="M1 1l4 4-4 4" fill="none" stroke="#fff" stroke-width="2"/></svg>BrisaLink</a>
  <a href="#"><svg width="7" height="10" viewBox="0 0 7 10"><path d="M1 1l4 4-4 4" fill="none" stroke="#fff" stroke-width="2"/></svg>Contact Us</a>
</nav>

<aside class="contact-box">
  <div class="contact-title">
    <svg width="46" height="46" viewBox="0 0 46 46" aria-hidden="true">
      <circle cx="23" cy="23" r="22" fill="#111" stroke="#ddd" stroke-width="2"/>
      <path d="M16 11c-3 2-4 6-2 11s6 10 10 12c3 1 6 1 8-1l-4-5-3 2c-2-1-5-5-6-8l3-2-3-6z" fill="#fff"/>
    </svg>
    <h2>Contact<br>Velmora Tech</h2>
  </div>
  <dl>
    <div class="row"><dt>Call us :</dt><dd>555 014 2290</dd></div>
    <div class="row"><dt>Fax &nbsp;&nbsp;:</dt><dd>555 014 2291</dd></div>
    <div class="row email"><dt>Email</dt><dd>info@velmoratechworks.example</dd></div>
  </dl>
</aside>

<section class="hero">
  <div class="hero-photo" role="img" aria-label="Engineers around a table reviewing an enclosure prototype beside a screen showing a 3D model"></div>
  <div class="hero-caption">A unique design, development and program<br>management company</div>
  <svg class="hero-next" width="30" height="30" viewBox="0 0 30 30" aria-label="Next slide">
    <circle cx="15" cy="15" r="14" fill="#f4f4f4"/>
    <path d="M12 9l6 6-6 6" fill="none" stroke="#444" stroke-width="3"/>
  </svg>
</section>

<main class="content">
  <h1>China Facilities</h1>
  <div class="intro">
    <p>Morbi porttitor arcu quis sapien porttitor faucibus. Nullam bibendum viverra lorem, luctus suscipit nulla facilisis in. Donec euismod magna quam, quis semper tortor luctus vel. Quisque erat erat, ornare eget pretium eget, hendrerit id magna. Cras dolor quam, faucibus id placerat a, mattis eu elit. Praesent ac lobortis nisl. Integer volutpat tempor eros vitae pulvinar. Praesent nec est iaculis, tincidunt mauris in, vehicula orci. Sed placerat felis risus, ut imperdiet augue adipiscing ac.</p>
    <div class="facility-photo" role="img" aria-label="Open-plan engineering office with rows of desks and workstations"></div>
  </div>
  <p class="body-para">Fusce quis dui at purus sodales vestibulum. Sed quam urna, scelerisque at turpis a, pellentesque interdum magna. Duis lacinia lectus justo, sit amet vulputate lorem semper nec. Fusce ipsum lectus, iaculis nec magna eu, gravida adipiscing dolor. Mauris tincidunt lectus nisl, eget rutrum mauris pharetra id. Cras consectetur laoreet leo, ut fermentum quam. Nullam porttitor lorem congue, volutpat lorem vitae, sodales dolor. Nullam mauris dui, pulvinar vel lacus nec, aliquet pharetra velit.</p>
  <ul class="service-list">
    <li>Custom Enclosure Design and Development</li>
    <li>Custom Antenna Design and Development</li>
    <li>Custom Connector Design and Development</li>
    <li>Custom Cable Assembly Design and Development</li>
    <li>Custom SMT PCB EMI Shield Walls and Covers</li>
    <li>Custom Membrane Switch Overlays</li>
    <li>Process Development and Testing</li>
  </ul>
</main>

<footer class="site-footer">
  <nav class="footer-nav">
    <a href="#">Home</a><span>|</span><a href="#">USA Facilities</a><span>|</span><a href="#">China Facilities</a><span>|</span><a href="#">Enclosures</a><span>|</span><a href="#">Antennas</a><span>|</span><a href="#">Connectors</a><span>|</span><a href="#">Cables</a><span>|</span><a href="#">EMI Shields</a><span>|</span><a href="#">Overlays</a><span>|</span><a href="#">Process Development</a><span>|</span><a href="#">BrisaLink</a><span>|</span><a href="#">Contact Us</a>
  </nav>
  <p class="copyright">Copyright &copy; 2013 &nbsp;Velmora Tech. &nbsp;&nbsp; All rights reserved.</p>
</footer>
</body>
</html>
```